Flag Order

We were just looking to order some branding flags to put on our rental equipment for our business. We would like different examples of the colors, shapes, sizes, backgrounds etc. Was thinking of just doing the plains icon instead of the whole logo on there. but open to ideas. preferably not a white background as they could get dirty,

```html
<!DOCTYPE html>
<html lang="en">
<head>
<meta charset="utf-8">
<title>Kestrel Equipment Rentals – Flag Designs</title>
<link rel="stylesheet" href="https://fonts.googleapis.com/css2?family=Montserrat:wght@400&family=Syncopate:wght@700&display=swap">
<style>
  :root {
    --ink: #222222;
    --brand-blue: #1a7bd0;
    --steel: #4f5861;
    --on-dark: #ffffff;
    --label-grey: #8a8a8a;
    --stand-grey: #9a9a9a;
    --paper: #ffffff;
  }
  * { margin: 0; padding: 0; box-sizing: border-box; }
  html, body { width: 1200px; height: 800px; overflow: hidden; background: var(--paper); }
  .canvas { position: relative; width: 1200px; height: 800px; }

  .hardware { position: absolute; inset: 0; }

  .design-label {
    position: absolute;
    font-family: "Montserrat", sans-serif;
    font-size: 11px;
    letter-spacing: 4px;
    color: var(--label-grey);
    transform: translateX(-50%);
    white-space: nowrap;
  }

  .flag {
    position: absolute;
    display: flex;
    align-items: center;
    justify-content: center;
    flex-direction: column;
  }
  .flag--ink   { background: var(--ink); }
  .flag--blue  { background: var(--brand-blue); }
  .flag--steel { background: var(--steel); }

  .brand-name { display: block; overflow: visible; }
  .brand-name text {
    font-family: "Syncopate", sans-serif;
    font-weight: 700;
    fill: var(--on-dark);
  }

  .brand-square { background: var(--brand-blue); }
  .brand-square--ink { background: var(--ink); }

  /* Design 1 – tall feather flag */
  .flag--tall { left: 100px; top: 97px; width: 140px; height: 560px; }
  .flag--tall .brand-name { position: absolute; left: 0; top: 0; }
  .flag--tall .brand-square { position: absolute; left: 30px; top: 432px; width: 90px; height: 96px; }

  /* Design 2 & 3 – wide pole flags */
  .flag--wide-logo { left: 303px; top: 113px; width: 274px; height: 167px; justify-content: flex-end; padding-bottom: 14px; }
  .flag--wide-mark { left: 618px; top: 113px; width: 274px; height: 167px; }
  .flag--wide-mark .brand-square { width: 98px; height: 98px; }

  /* Design 4 & 5 – small rectangle flags */
  .flag--small-logo { left: 779px; top: 420px; width: 141px; height: 235px; justify-content: flex-end; padding-bottom: 46px; }
  .flag--small-mark { left: 1022px; top: 420px; width: 139px; height: 235px; }
  .flag--small-mark .brand-square { width: 82px; height: 82px; }
</style>
</head>
<body>
<main class="canvas">

  <svg class="hardware" width="1200" height="800" viewBox="0 0 1200 800" aria-hidden="true">
    <g class="poles" fill="#111">
      <rect x="93" y="100" width="7" height="560"/>
      <rect x="92" y="96" width="148" height="4"/>
      <rect x="95" y="660" width="4" height="52"/>
      <circle cx="297" cy="102" r="7"/>
      <rect x="293" y="106" width="8" height="554"/>
      <rect x="295" y="660" width="4" height="52"/>
      <circle cx="613" cy="102" r="7"/>
      <rect x="609" y="106" width="8" height="554"/>
      <rect x="611" y="660" width="4" height="52"/>
      <rect x="772" y="420" width="7" height="240"/>
      <rect x="771" y="416" width="149" height="4"/>
      <rect x="774" y="660" width="4" height="52"/>
      <rect x="1015" y="420" width="7" height="240"/>
      <rect x="1014" y="416" width="147" height="4"/>
      <rect x="1017" y="660" width="4" height="52"/>
    </g>
    <g class="stands" stroke="var(--stand-grey)" stroke-width="2" fill="none" stroke-linecap="round">
      <g transform="translate(97,715)"><path d="M0 0 L-68 8 M0 0 L-42 40 M0 0 L74 30 M0 0 L44 -6"/><rect x="-5" y="-6" width="10" height="12" fill="#bbb"/></g>
      <g transform="translate(297,715)"><path d="M0 0 L-68 8 M0 0 L-42 40 M0 0 L74 30 M0 0 L44 -6"/><rect x="-5" y="-6" width="10" height="12" fill="#bbb"/></g>
      <g transform="translate(613,715)"><path d="M0 0 L-68 8 M0 0 L-42 40 M0 0 L74 30 M0 0 L44 -6"/><rect x="-5" y="-6" width="10" height="12" fill="#bbb"/></g>
      <g transform="translate(776,715)"><path d="M0 0 L-68 8 M0 0 L-42 40 M0 0 L74 30 M0 0 L44 -6"/><rect x="-5" y="-6" width="10" height="12" fill="#bbb"/></g>
      <g transform="translate(1019,715)"><path d="M0 0 L-68 8 M0 0 L-42 40 M0 0 L74 30 M0 0 L44 -6"/><rect x="-5" y="-6" width="10" height="12" fill="#bbb"/></g>
    </g>
  </svg>

  <p class="design-label" style="left:162px; top:50px;">DESIGN #1</p>
  <p class="design-label" style="left:440px; top:50px;">DESIGN #2</p>
  <p class="design-label" style="left:758px; top:50px;">DESIGN #3</p>
  <p class="design-label" style="left:843px; top:369px;">DESIGN #4</p>
  <p class="design-label" style="left:1087px; top:369px;">DESIGN #5</p>

  <section class="flag flag--tall flag--ink" aria-label="Design 1 feather flag">
    <svg class="brand-name" width="140" height="560" viewBox="0 0 140 560" role="img" aria-label="Kestrel Equipment Rentals">
      <text transform="translate(82,404) rotate(-90)" font-size="56" textLength="376" lengthAdjust="spacingAndGlyphs">KESTREL</text>
      <text transform="translate(112,404) rotate(-90)" font-size="17" textLength="376" lengthAdjust="spacing">EQUIPMENT RENTALS</text>
    </svg>
    <div class="brand-square"></div>
  </section>

  <section class="flag flag--wide-logo flag--blue" aria-label="Design 2 flag">
    <svg class="brand-name" width="164" height="36" viewBox="0 0 164 36" role="img" aria-label="Kestrel Equipment Rentals">
      <text x="1" y="22" font-size="24" textLength="162" lengthAdjust="spacingAndGlyphs">KESTREL</text>
      <text x="1" y="34" font-size="7" textLength="162" lengthAdjust="spacing">EQUIPMENT RENTALS</text>
    </svg>
  </section>

  <section class="flag flag--wide-mark flag--ink" aria-label="Design 3 flag">
    <div class="brand-square"></div>
  </section>

  <section class="flag flag--small-logo flag--steel" aria-label="Design 4 flag">
    <svg class="brand-name" width="119" height="28" viewBox="0 0 119 28" role="img" aria-label="Kestrel Equipment Rentals">
      <text x="1" y="17" font-size="18" textLength="117" lengthAdjust="spacingAndGlyphs">KESTREL</text>
      <text x="1" y="26" font-size="5.5" textLength="117" lengthAdjust="spacing">EQUIPMENT RENTALS</text>
    </svg>
  </section>

  <section class="flag flag--small-mark flag--blue" aria-label="Design 5 flag">
    <div class="brand-square brand-square--ink"></div>
  </section>

</main>
</body>
</html>
```